Business card for a new cabinet shop company named Veloran Cabinets for high end cabinets

Design a business card, thinking dark rich green with colours to speak of high end luxury ie; cream, gold, black possibly

Mitchell Tarrowby
Director Craftsman
Email: info@veloranjoinery-example.com.au
Instagram : @veloran.cabinets

```html
<!DOCTYPE html>
<html lang="en">
<head>
<meta charset="utf-8">
<title>Veloran Cabinets – Business Card</title>
<link rel="stylesheet" href="https://fonts.googleapis.com/css2?family=Roboto:wght@300;400;500;700&display=swap">
<style>
  :root {
    --page-bg: #f1f0f0;
    --card-bg: #212125;
    --gold: #c9ab67;
    --green: #14954a;
    --white: #f4f4f4;
    --card-radius: 40px;
  }
  * { box-sizing: border-box; margin: 0; padding: 0; }
  html, body {
    width: 1200px;
    height: 990px;
    overflow: hidden;
    background: var(--page-bg);
    font-family: "Roboto", Arial, sans-serif;
  }
  .card {
    position: absolute;
    left: 245px;
    width: 711px;
    height: 406px;
    background: var(--card-bg);
    border-radius: var(--card-radius);
    border-left: 4px solid var(--gold);
    border-bottom: 4px solid var(--gold);
    overflow: hidden;
  }
  .card--front { top: 68px; }
  .card--back { top: 516px; }

  .wordmark {
    position: absolute;
    display: flex;
    align-items: center;
    color: var(--gold);
    font-weight: 500;
    white-space: nowrap;
  }
  .wordmark__square {
    background: var(--gold);
    flex: none;
  }
  .card--front .wordmark {
    left: 50%;
    top: 50%;
    transform: translate(-50%, -50%);
    font-size: 50px;
    gap: 24px;
  }
  .card--front .wordmark__square { width: 40px; height: 40px; }

  .card--back .wordmark {
    left: 30px;
    top: 184px;
    font-size: 30px;
    gap: 14px;
  }
  .card--back .wordmark__square { width: 24px; height: 24px; }

  .divider {
    position: absolute;
    left: 354px;
    top: 76px;
    width: 1px;
    height: 250px;
    background: var(--gold);
    opacity: 0.8;
  }

  .contact {
    position: absolute;
    left: 396px;
    top: 132px;
    width: 284px;
  }
  .contact__name {
    font-size: 30px;
    line-height: 1;
    font-weight: 300;
    color: var(--green);
    white-space: nowrap;
  }
  .contact__name strong { color: var(--gold); font-weight: 500; }
  .contact__role {
    margin-top: 8px;
    font-size: 17px;
    color: var(--white);
  }
  .contact__list {
    list-style: none;
    margin-top: 22px;
  }
  .contact__item {
    display: flex;
    align-items: center;
    gap: 9px;
    height: 24px;
    font-size: 14.5px;
    letter-spacing: 0;
    color: var(--white);
    white-space: nowrap;
  }
  .contact__icon { width: 15px; height: 15px; flex: none; }
</style>
</head>
<body>

  <section class="card card--front">
    <div class="wordmark">
      <span class="wordmark__square"></span>
      <span class="wordmark__name">Veloran Cabinets</span>
    </div>
  </section>

  <section class="card card--back">
    <div class="wordmark">
      <span class="wordmark__square"></span>
      <span class="wordmark__name">Veloran Cabinets</span>
    </div>

    <div class="divider"></div>

    <div class="contact">
      <h1 class="contact__name"><strong>Mitchell</strong> Tarrowby</h1>
      <p class="contact__role">Director Craftsman</p>
      <ul class="contact__list">
        <li class="contact__item">
          <svg class="contact__icon" viewBox="0 0 16 16" aria-hidden="true">
            <circle cx="8" cy="8" r="6.5" fill="none" stroke="#c9ab67" stroke-width="1.5"/>
          </svg>
          @veloran.cabinets
        </li>
        <li class="contact__item">
          <svg class="contact__icon" viewBox="0 0 16 16" aria-hidden="true">
            <rect x="1" y="3.5" width="14" height="10" fill="none" stroke="#c9ab67" stroke-width="1.4"/>
            <path d="M1 3.5 L8 9 L15 3.5" fill="none" stroke="#c9ab67" stroke-width="1.4"/>
          </svg>
          info@veloranjoinery-example.com.au
        </li>
        <li class="contact__item">
          <svg class="contact__icon" viewBox="0 0 16 16" aria-hidden="true">
            <circle cx="8" cy="8" r="6.5" fill="none" stroke="#c9ab67" stroke-width="1.4"/>
            <ellipse cx="8" cy="8" rx="3" ry="6.5" fill="none" stroke="#c9ab67" stroke-width="1.1"/>
            <line x1="1.5" y1="8" x2="14.5" y2="8" stroke="#c9ab67" stroke-width="1.1"/>
          </svg>
          www.veloranjoinery-example.com.au
        </li>
      </ul>
    </div>
  </section>

</body>
</html>
```